Restyle corporate identity (+ logo) for a road construction company

We need a new logo and stationary design for our company VARNOK path. VARNOK path® increases the road base strength, while reducing major costs and time of road construction. Attached some examples of the current design.

Our wishes for the new logo:
- Business look
- Style sheet
- Modern

More information: www.varnokpath.example
Updates

Target Market(s)

Government

Industry/Entity Type

Construction

Requirements
Must have
• Logo (with road sign) + text

```html
<!DOCTYPE html>
<html lang="en">
<head>
<meta charset="utf-8">
<title>VARNOK path – Stationery</title>
<link href="https://fonts.googleapis.com/css2?family=Montserrat:wght@500&family=Open+Sans:wght@400;600;700&display=swap" rel="stylesheet">
<style>
  :root {
    --green: #9bc43f;
    --grey: #8a8a8d;
    --grey-light: #f3f3f3;
    --dark: #414244;
    --text: #5b5b5d;
    --bg: #dcdcdc;
    --road: linear-gradient(160deg, #e9e9ea 0%, #d7d7d9 60%, #e6e6e7 100%);
  }
  * { box-sizing: border-box; margin: 0; padding: 0; }
  html, body { width: 1200px; height: 1048px; overflow: hidden; }
  body {
    position: relative;
    background: radial-gradient(circle at 50% 40%, #ececec 0%, var(--bg) 100%);
    font-family: "Open Sans", Arial, sans-serif;
    color: var(--text);
  }
  .sheet { position: absolute; background: #fff; overflow: hidden; box-shadow: 0 6px 18px rgba(0,0,0,.22); }

  /* wordmark: one colour, one weight, plain square beside it */
  .wordmark { display: flex; align-items: center; gap: 10px; font-family: "Montserrat", Arial, sans-serif; font-weight: 500; color: var(--grey); white-space: nowrap; }
  .wordmark .mark-square { background: var(--green); flex: none; }
  .wordmark.on-dark { color: #fff; }

  .road-illustration { position: absolute; background: var(--road); border-radius: 50% 0 0 0; }

  /* envelope */
  .envelope { left: 40px; top: 40px; width: 560px; height: 250px; background: var(--grey-light); }
  .envelope .band-top { position: absolute; right: 0; top: 0; width: 325px; height: 22px; background: var(--green); border-bottom-left-radius: 22px; }
  .envelope .band-bottom-grey { position: absolute; right: 0; bottom: 0; width: 330px; height: 18px; background: var(--grey); }
  .envelope .band-bottom-green { position: absolute; left: 0; bottom: 0; width: 360px; height: 22px; background: var(--green); border-top-right-radius: 22px; }
  .envelope .road-illustration { right: 0; bottom: 18px; width: 140px; height: 140px; }
  .envelope .wordmark { position: absolute; left: 24px; top: 58px; font-size: 26px; }
  .envelope .wordmark .mark-square { width: 26px; height: 26px; }
  .envelope .address { position: absolute; left: 24px; top: 150px; font-size: 9.5px; line-height: 1.35; white-space: nowrap; }
  .address .lines { font-weight: 600; }
  .address .label { color: var(--green); }
  .envelope .address .label { display: inline-block; width: 30px; }
  .address .contact { font-size: 8px; margin-top: 2px; }
  .envelope .web { position: absolute; right: 18px; bottom: 24px; font-size: 9.5px; }

  /* letterhead */
  .letterhead { left: 650px; top: 40px; width: 510px; height: 720px; }
  .letterhead .band-top-grey { position: absolute; left: 0; top: 0; width: 230px; height: 12px; background: var(--grey); }
  .letterhead .band-top-green { position: absolute; right: 0; top: 0; width: 290px; height: 30px; background: var(--green); border-bottom-left-radius: 30px; }
  .letterhead .rule { position: absolute; left: 40px; right: 40px; height: 1px; background: #9a9a9a; }
  .letterhead .rule.top { top: 62px; }
  .letterhead .rule.bottom { bottom: 112px; }
  .letterhead .wordmark { position: absolute; left: 0; right: 0; top: 84px; justify-content: center; font-size: 34px; }
  .letterhead .wordmark .mark-square { width: 34px; height: 34px; }
  .letterhead .road-illustration { right: 0; bottom: 30px; width: 300px; height: 270px; }
  .letterhead .address { position: absolute; left: 60px; bottom: 42px; font-size: 9.5px; line-height: 1.5; white-space: nowrap; }
  .letterhead .address .lines { font-size: 13px; font-weight: 700; color: var(--text); margin-bottom: 2px; }
  .letterhead .address .gap { display: inline-block; width: 18px; }
  .letterhead .band-bottom-grey { position: absolute; right: 0; bottom: 0; width: 290px; height: 22px; background: var(--grey); }
  .letterhead .band-bottom-green { position: absolute; left: 0; bottom: 0; width: 240px; height: 30px; background: var(--green); border-top-right-radius: 30px; }

  /* business cards */
  .card { width: 280px; height: 160px; }
  .card-front { left: 40px; top: 340px; background: var(--dark); }
  .card-front .wordmark { position: absolute; left: 0; right: 0; top: 52px; justify-content: center; font-size: 22px; }
  .card-front .wordmark .mark-square { width: 22px; height: 22px; }
  .card-front .rule { position: absolute; left: 20px; right: 20px; top: 104px; height: 1px; background: var(--green); }
  .card-front .web { position: absolute; right: 20px; bottom: 16px; font-size: 8px; color: var(--green); }

  .card-back { left: 340px; top: 340px; }
  .card-back .wordmark { position: absolute; left: 16px; top: 16px; font-size: 18px; }
  .card-back .wordmark .mark-square { width: 18px; height: 18px; }
  .card-back .person { position: absolute; left: 16px; top: 50px; font-size: 9px; font-weight: 700; }
  .card-back .person span { display: block; font-size: 7px; font-weight: 400; color: var(--green); }
  .card-back .rule { position: absolute; left: 16px; right: 16px; top: 76px; height: 1px; background: var(--green); }
  .card-back .road-illustration { right: 0; top: 70px; width: 110px; height: 70px; }
  .card-back .band-green { position: absolute; left: 0; bottom: 0; width: 150px; height: 48px; background: var(--green); border-top-right-radius: 26px; }
  .card-back .band-green p { color: #fff; font-size: 7px; line-height: 1.4; padding: 8px 12px; }
  .card-back .band-dark { position: absolute; right: 0; bottom: 0; width: 140px; height: 14px; background: var(--dark); }
  .card-back .contact-list { position: absolute; left: 164px; top: 84px; font-size: 7px; line-height: 1.5; list-style: none; white-space: nowrap; }
  .card-back .contact-list li::before { content: ""; display: inline-block; width: 6px; height: 6px; background: var(--green); margin-right: 5px; vertical-align: -1px; }

  /* logo lockups */
  .lockup-horizontal { position: absolute; left: 80px; top: 860px; display: flex; align-items: center; gap: 26px; }
  .lockup-horizontal .mark-square { width: 90px; height: 90px; background: var(--green); }
  .lockup-horizontal .divider { width: 2px; height: 110px; background: var(--grey); }
  .lockup-horizontal .wordmark { font-size: 48px; }

  .lockup-stacked { position: absolute; left: 760px; width: 420px; top: 800px; display: flex; flex-direction: column; align-items: center; gap: 22px; }
  .lockup-stacked .mark-square { width: 110px; height: 110px; background: var(--green); }
  .lockup-stacked .wordmark { font-size: 46px; }
</style>
</head>
<body>

  <section class="sheet envelope" aria-label="Envelope">
    <div class="band-top"></div>
    <div class="road-illustration" role="img" aria-label="Grey winding road illustration"></div>
    <div class="wordmark"><span class="mark-square"></span>VARNOK path</div>
    <div class="address">
      <p class="lines">Address Line 1, Address Line2,<br>Address Line 3</p>
      <p class="contact"><span class="label">Email -</span> yourmail@varnokpath.example</p>
      <p class="contact"><span class="label">Tel.</span> - +123 456 780</p>
      <p class="contact"><span class="label">Fax.</span> - +123 456 789</p>
    </div>
    <p class="web">www.varnokpath.example</p>
    <div class="band-bottom-grey"></div>
    <div class="band-bottom-green"></div>
  </section>

  <section class="sheet letterhead" aria-label="Letterhead">
    <div class="band-top-grey"></div>
    <div class="band-top-green"></div>
    <div class="rule top"></div>
    <div class="wordmark"><span class="mark-square"></span>VARNOK path</div>
    <div class="road-illustration" role="img" aria-label="Grey winding road illustration"></div>
    <div class="rule bottom"></div>
    <div class="address">
      <p class="lines">Address Line 1, Address Line2, Address Line 3</p>
      <p><span class="label">Email -</span> yourmail@varnokpath.example<span class="gap"></span><span class="label">WEB -</span> www.varnokpath.example</p>
      <p><span class="label">Tel. -</span> +123 456 780<span class="gap"></span><span class="label">Fax. -</span> +123 456 789</p>
    </div>
    <div class="band-bottom-grey"></div>
    <div class="band-bottom-green"></div>
  </section>

  <section class="sheet card card-front" aria-label="Business card front">
    <div class="wordmark on-dark"><span class="mark-square"></span>VARNOK path</div>
    <div class="rule"></div>
    <p class="web">www.varnokpath.example</p>
  </section>

  <section class="sheet card card-back" aria-label="Business card back">
    <div class="wordmark"><span class="mark-square"></span>VARNOK path</div>
    <p class="person">YOUR NAME<span>Position</span></p>
    <div class="rule"></div>
    <div class="road-illustration" role="img" aria-label="Grey winding road illustration"></div>
    <ul class="contact-list">
      <li>+123 456 780</li>
      <li>+123 456 789</li>
      <li>yourmail@varnokpath.example</li>
      <li>www.varnokpath.example</li>
    </ul>
    <div class="band-dark"></div>
    <div class="band-green"><p>Address Line 1, Address Line 2,<br>Address Line 3</p></div>
  </section>

  <div class="lockup-horizontal" aria-label="Horizontal logo lockup">
    <span class="mark-square"></span>
    <span class="divider"></span>
    <span class="wordmark">VARNOK path</span>
  </div>

  <div class="lockup-stacked" aria-label="Stacked logo lockup">
    <span class="mark-square"></span>
    <span class="wordmark">VARNOK path</span>
  </div>

</body>
</html>
```